Pennavault Web Design Project

We will need only one logo for Pennavault
Front Page
Header - Pennavault (logo) - Sites - Categories - Featured Contributors - Login (end header - the way markmaven does this is great, but I'm open to new ideas also)
(Start Page Content)
Pennavault (logo - centered)
weeklyoddments.com - thequickpost.com - stokingember.com (please leave spaces where we can place screenshots of those pages)
Sign Up!
Pennavault is a constantly growing network of sites that are dedicated to create relevant and well written content. If you are a student, professional, or a retiree, and you have an idea about a website that you would like to Contribute to, then this is the community that you have been looking for.
How It Works
Contribute An Article - Get Published - Increase Your Digital Footprint
Why We Exist
In the days when newspapers and radio stations dictated what the public read and heard, writers and editors were the gatekeepers in front of knowledge.
Those days are over and the lines between people who read content and publish content have become blurred. The outer-space like vastness of the internet is made larger exponentially every second by people who contribute data to it.
We believe that the future of knowledge in this world will have no gatekeepers and that every person is a contributor. This belief has lead to the creation of Pennavault.
Pennavault (logo-centered) - By The People, For The People
Footer
Follow Us: facebook, twitter, google+, youtube, instagram, linked in
____________________________
Categories Page (will need it's own page)
Arts & Entertainment - weeklyoddments.com
Health & Fitness - stokingember.com
News - thequickpost.com
If you’re interested in contributing to a topic listed below please email us at info@pennavault.com
Automotive
Business
Careers
Education
Family & Parenting
Personal Finance
Food & Drink
Hobbies & Interests
Home & Garden
Law, Government & Politics
Society
Science
Pets
Sports
Style & Fashion
Technology & Computing
Travel
Real Estate
Shopping
Religion and Spirituality
Uncategorized
___________________________
Sites Page (will need it's own page)
Weekly Oddments - weeklyoddments.com is an Arts & Entertainment website consisting of photo galleries and descriptions.
The Quickpost - thequickpost.com is a News website that is specifically dedicated to newly trending topics.
Stoking Ember - stokingember.com is a Health & Fitness website where visitors can find articles about workout routines, health supplements, and get ideas for eating clean.
_________________________
Featured Contributors Page (will need it's own page)
Content is to be determined
__________________________
NOTES FOR DESIGNER
We also will need a two column sub page that with one column being thin for navigation. We really like the simplicity of tidelume.com and markmaven.com. Those are two sites you can reference for the direcion we are heading in.
Thanks!
-Tommy
Updates
Hey Everyone!

```html
<!DOCTYPE html>
<html lang="en">
<head>
<meta charset="utf-8">
<title>Pennavault</title>
<link href="https://fonts.googleapis.com/css2?family=Open+Sans:wght@300;400;600;700&display=swap" rel="stylesheet">
<style>
:root{
  --olive:#9c9c2c;
  --olive-text:#a3a33a;
  --olive-light:#c9c93a;
  --hero-bg:#e4e4d0;
  --curve-line:#c2c2a6;
  --ink:#3b3b3b;
  --muted:#a8a8a8;
  --soft-bg:#f4f4f4;
  --band:#9a9a9a;
  --footer-ink:#777;
  --white:#fff;
}
*{margin:0;padding:0;box-sizing:border-box}
html,body{width:1200px;height:2299px;overflow:hidden}
body{font-family:"Open Sans",Arial,sans-serif;background:var(--soft-bg);position:relative;color:var(--ink)}

.hero{position:absolute;left:0;top:0;width:1200px;height:598px;background:var(--hero-bg)}
.hero-curve{position:absolute;left:0;top:0}
.main-nav{position:absolute;top:29px;left:0;width:1200px;text-align:center;font-size:15px;color:#555}
.main-nav a{color:inherit;text-decoration:none;margin:0 9px}
.brand{font-weight:700;color:var(--ink);letter-spacing:.5px}
.hero .brand{position:absolute;top:66px;left:0;width:1200px;text-align:center;font-size:34px}

.site-card{position:absolute;top:204px;width:220px;text-align:center}
.site-card svg{display:block;margin:0 auto}
.site-card span{display:block;margin-top:20px;font-size:14px;color:var(--olive-text)}

.signup{position:absolute;left:524px;top:483px;width:150px;height:59px;border-radius:28px;background:var(--olive);border-bottom:4px solid var(--olive-light);color:var(--white);font-weight:700;font-size:25px;text-align:center;line-height:55px}

.intro{position:absolute;left:0;top:598px;width:1200px;height:234px;background:linear-gradient(160deg,#f1f1f1 0%,#fff 35%,#fff 70%,#f6f6f6 100%)}
.intro p{position:absolute;left:187px;top:75px;width:826px;font-size:16px;line-height:30.5px;color:var(--muted);font-weight:300}

.how{position:absolute;left:0;top:832px;width:1200px;height:437px;background:var(--soft-bg);text-align:center}
.how h2{margin-top:75px;font-weight:300;font-size:35px;color:#999;letter-spacing:1px}
.step{position:absolute;top:164px;width:300px;text-align:center}
.step svg{display:block;margin:0 auto;height:132px}
.step h3{margin-top:32px;font-weight:400;font-size:24px;color:var(--olive-text)}

.why{position:absolute;left:0;top:1269px;width:1200px;height:413px;background:var(--band);color:var(--white);text-align:center}
.why h2{margin-top:46px;font-weight:400;font-size:35px}
.why p{margin:30px auto 0;width:826px;font-size:15.5px;line-height:19.6px;text-align:justify}
.why .brand{display:block;color:var(--white);margin-top:32px;font-size:34px}
.why .tagline{font-weight:600;font-size:16px;margin-top:0}

.footer{position:absolute;left:0;top:1682px;width:1200px;height:617px;background:var(--soft-bg);color:var(--footer-ink);font-size:12.5px;line-height:15.6px}
.follow{position:absolute;top:18px;width:1200px;text-align:center;font-size:18px;color:#666}
.social{position:absolute;top:55px;left:477px;display:flex;gap:11px}
.social span{width:33px;height:33px;border-radius:3px}
.col{position:absolute;top:112px}
.col-left{left:184px;width:400px}
.col-right{left:609px;width:420px}
.col h4{font-weight:700;font-size:13px;margin-bottom:16px}
.col p{margin-bottom:15.6px}
.col ul{list-style:none}
.col b{font-weight:700}
.copyright{position:absolute;top:589px;width:1200px;text-align:center;font-size:11.5px;color:#999}
</style>
</head>
<body>

<header class="hero">
  <svg class="hero-curve" width="1200" height="150" viewBox="0 0 1200 150">
    <path d="M0 0 H1200 V32 C1080 40 960 70 850 110 C760 140 680 140 600 138 C520 140 440 140 350 110 C240 70 120 40 0 32 Z" fill="#fafafa" stroke="var(--curve-line)" stroke-width="2"/>
  </svg>
  <nav class="main-nav">
    <a href="#">Sites</a><a href="#">Categories</a><a href="#">Featured Contributors</a><a href="#">Login</a>
  </nav>
  <div class="brand">Pennavault</div>

  <div class="site-card" style="left:77px">
    <svg width="180" height="168" viewBox="0 0 180 168" role="img" aria-label="Screenshot space for weeklyoddments.com"><polygon points="45,0 90,20 135,0 160,45 180,84 160,123 135,168 90,148 45,168 20,123 0,84 20,45" fill="#fff"/></svg>
    <span>weeklyoddments.com</span>
  </div>
  <div class="site-card" style="left:489px">
    <svg width="180" height="168" viewBox="0 0 180 168" role="img" aria-label="Screenshot space for thequickpost.com"><polygon points="45,0 90,20 135,0 160,45 180,84 160,123 135,168 90,148 45,168 20,123 0,84 20,45" fill="#fff"/></svg>
    <span>thequickpost.com</span>
  </div>
  <div class="site-card" style="left:900px">
    <svg width="180" height="168" viewBox="0 0 180 168" role="img" aria-label="Screenshot space for stokingember.com"><polygon points="45,0 90,20 135,0 160,45 180,84 160,123 135,168 90,148 45,168 20,123 0,84 20,45" fill="#fff"/></svg>
    <span>stokingember.com</span>
  </div>

  <a class="signup" href="#">Sign Up!</a>
</header>

<section class="intro">
  <p>Pennavault is a constantly growing network of sites that are dedicated to create relevant and well written content. If you are a student, professional, or a retiree, and you have an idea about a website that you would like to Contribute to, then this is the community that you have been looking for.</p>
</section>

<section class="how">
  <h2>HOW IT WORKS</h2>
  <div class="step" style="left:195px">
    <svg viewBox="0 0 110 132" width="110">
      <rect x="5" y="2" width="100" height="128" rx="4" fill="var(--olive)"/>
      <path d="M80 130 L105 105 V126 a4 4 0 0 1 -4 4 Z" fill="#e8e8e0"/>
      <rect x="22" y="22" width="66" height="5" fill="#f1f1e0"/>
      <rect x="22" y="38" width="66" height="5" fill="#f1f1e0"/>
      <rect x="22" y="54" width="66" height="5" fill="#f1f1e0"/>
      <rect x="22" y="70" width="66" height="5" fill="#f1f1e0"/>
    </svg>
    <h3>Contribute An Article</h3>
  </div>
  <div class="step" style="left:449px">
    <svg viewBox="0 0 120 132" width="120">
      <polygon points="20,55 95,10 108,95 30,85" fill="#e6e6dc"/>
      <rect x="10" y="55" width="22" height="32" rx="4" fill="var(--olive)"/>
      <rect x="30" y="82" width="14" height="46" rx="4" fill="var(--olive)" transform="rotate(-18 37 105)"/>
      <circle cx="108" cy="55" r="10" fill="var(--olive)"/>
    </svg>
    <h3>Get Published</h3>
  </div>
  <div class="step" style="left:707px">
    <svg viewBox="0 0 110 132" width="110">
      <polygon points="38,2 72,2 64,26 46,26" fill="#bdbdb4"/>
      <rect x="42" y="24" width="26" height="8" fill="var(--olive)"/>
      <ellipse cx="55" cy="88" rx="48" ry="44" fill="#c9c9c0"/>
      <text x="55" y="108" text-anchor="middle" font-family="Open Sans, sans-serif" font-weight="700" font-size="56" fill="var(--olive)">$</text>
    </svg>
    <h3>Reap The Benefits</h3>
  </div>
</section>

<section class="why">
  <h2>Why We Exist</h2>
  <p>In the days when newspapers and radio stations dictated what the public read and heard, writers and editors were the gatekeepers in front of knowledge.<br>Those days are over and the lines between people who read content and publish content have become blurred. The outer-space like vastness of the internet is made larger exponentially every second by people who contribute data to it.<br>We believe that the future of knowledge in this world will have no gatekeepers and that every person is a contributor. This belief has lead to the creation of Pennavault</p>
  <span class="brand">Pennavault</span>
  <p class="tagline" style="text-align:center;margin-top:0">By The People, For The People</p>
</section>

<footer class="footer">
  <div class="follow">Follow Us:</div>
  <div class="social">
    <span style="background:#3b5a9a"></span>
    <span style="background:#4aa3dc"></span>
    <span style="background:#3a3a3a"></span>
    <span style="background:#c4302b"></span>
    <span style="background:#7a5a45"></span>
    <span style="background:#2a75ae"></span>
  </div>

  <div class="col col-left">
    <h4>Categories Page</h4>
    <p>Arts &amp; Entertainment - weeklyoddments.com<br>Health &amp; Fitness - stokingember.com<br>News - thequickpost.com</p>
    <p>If you’re interested in contributing to a topic<br>listed below please email us at info@pennavault.com</p>
    <ul>
      <li>Automotive</li><li>Business</li><li>Careers</li><li>Education</li><li>Family &amp; Parenting</li><li>Personal Finance</li><li>Food &amp; Drink</li><li>Hobbies &amp; Interests</li><li>Home &amp; Garden</li><li>Law, Government &amp; Politics</li><li>Society</li><li>Science</li><li>Pets</li><li>Sports</li><li>Style &amp; Fashion</li><li>Technology &amp; Computing</li><li>Travel</li><li>Real Estate</li><li>Shopping</li><li>Religion and Spirituality</li><li>Uncategorized</li>
    </ul>
  </div>

  <div class="col col-right">
    <h4>Sites Page</h4>
    <p><b>Weekly Oddments</b> - weeklyoddments.com is an Arts &amp; Entertainment<br>website consisting of photo galleries and descriptions.</p>
    <p><b>The Quickpost</b> - thequickpost.com is a News website that is specifically<br>dedicated to newly trending topics.</p>
    <p><b>Stoking Ember</b> - stokingember.com is a Health &amp; Fitness website where<br>visitors can find articles about workout routines, health supplements,<br>and get ideas for eating clean.</p>
    <h4 style="margin-top:22px">Featured Contributors Page</h4>
  </div>

  <div class="copyright">© 2013 All Rights Reserved</div>
</footer>

</body>
</html>
```